RM Tomás Ledesma (Business Card)

Hi designers, in this work, I'm looking for an sophisticated stylish, elegant and proffesional personal card. We have a laboratory of pathology automated, with equipments high quality.
In this web the designers, have created my business logo, the name is "RM Tomás Ledesma"
In our lab, we principal work is to prepare the biopsies for further diagnostic of diseases like cancer, tumors, etc.
I need that the first face, only having my complete logo (Rm Tomás Ledesma, Laboratorio de procesamiento Histologico)
The overleaf, could repeat the same logo, like water logo.
In this face, I need to say: My full data:

Técnico en Anatomía Patológica
Tomás Ledesma Urquiza M.P 48213
Av. Duarte Quirós 817 - 2do piso - Instituto Brandsen.
Córdoba, Argentina
(0351) 158246093
ledesma.tomas@correoviva.com.ar

with respect the colors of card, use your imagination, the original logo color is violet, I haven't chosen a color base for the card.

attached pictures are examples of cards I like your DESIGN.
Attached too, the original logo to my company.

the size of card are:
horizontal: 9cm
vertical: 5,5cm

any question that you have, not doubt to question me,
Hand to work!

Industry/Entity Type

Laboratory

Requirements
Must have
• designers sophisticated, not simples, like show the images attached

```html
<!DOCTYPE html>
<html lang="es">
<head>
<meta charset="utf-8">
<title>Tomás Ledesma – Tarjeta personal</title>
<link rel="stylesheet" href="https://fonts.googleapis.com/css2?family=Exo+2:wght@500;600;700&family=Open+Sans:wght@400;600&display=swap">
<style>
  :root{
    --violet:#7a2f93;
    --violet-deep:#5e1f78;
    --violet-light:#9a4db3;
    --ink-grey:#6f6f73;
    --card-white:#ffffff;
    --page:#e8e6eb;
  }
  *{margin:0;padding:0;box-sizing:border-box}
  html,body{width:1200px;height:1000px;overflow:hidden;background:var(--page)}
  .sheet{position:relative;width:1200px;height:1000px}
  .card{
    position:absolute;left:240px;width:720px;height:440px;
    background:var(--card-white);
    box-shadow:0 6px 22px rgba(60,40,70,.18);
    overflow:hidden;
  }
  .card--front{top:36px}
  .card--back{top:524px}

  /* front face: brand lockup */
  .brand{
    position:absolute;left:0;right:0;top:150px;
    display:flex;flex-direction:column;align-items:center;
  }
  .brand__row{display:flex;align-items:center;gap:14px}
  .brand__square{width:34px;height:34px;background:var(--violet)}
  .brand__name{
    font-family:"Open Sans",sans-serif;font-weight:600;font-size:36px;
    color:var(--violet);letter-spacing:.04em;
  }
  .brand__rule{width:420px;height:1px;background:var(--ink-grey);margin:14px 0 8px}
  .brand__tagline{
    font-family:"Open Sans",sans-serif;font-weight:600;font-size:19px;
    color:var(--ink-grey);text-transform:uppercase;
  }

  /* back face */
  .back-art{position:absolute;inset:0}
  .watermark{
    position:absolute;left:20px;top:38px;width:320px;
    display:flex;flex-direction:column;align-items:center;opacity:.55;
  }
  .watermark__name{
    font-family:"Open Sans",sans-serif;font-weight:600;font-size:22px;
    color:var(--violet-light);letter-spacing:.04em;
  }
  .watermark__rule{width:290px;height:1px;background:var(--ink-grey);margin:6px 0 4px}
  .watermark__tagline{
    font-family:"Open Sans",sans-serif;font-weight:600;font-size:12px;
    color:var(--ink-grey);text-transform:uppercase;white-space:nowrap;
  }
  .details{font-family:"Exo 2",sans-serif;color:var(--violet)}
  .details p{position:absolute;white-space:nowrap}
  .details__name{
    right:20px;top:176px;
    font-weight:700;font-size:21px;letter-spacing:.01em;
  }
  .details__role{
    right:60px;top:208px;
    font-weight:600;font-size:14px;
  }
  .details__email{
    right:26px;top:250px;
    font-weight:600;font-size:14px;letter-spacing:.02em;
  }
  .details__address{
    left:312px;top:288px;
    font-weight:600;font-size:15px;line-height:22px;letter-spacing:.02em;
  }
  .details__phone{
    left:290px;top:360px;
    font-weight:600;font-size:16px;letter-spacing:.04em;
  }
</style>
</head>
<body>
<main class="sheet">

  <section class="card card--front" aria-label="Frente de la tarjeta">
    <div class="brand">
      <div class="brand__row">
        <span class="brand__square"></span>
        <span class="brand__name">RM Tomás Ledesma</span>
      </div>
      <span class="brand__rule"></span>
      <span class="brand__tagline">Laboratorio de Procesamiento Histológico</span>
    </div>
  </section>

  <section class="card card--back" aria-label="Dorso de la tarjeta">
    <svg class="back-art" width="720" height="440" viewBox="0 0 720 440">
      <defs>
        <linearGradient id="greyField" x1="0" y1="0" x2="0.4" y2="1">
          <stop offset="0" stop-color="#f4f4f5"/>
          <stop offset="1" stop-color="#c8c8cb"/>
        </linearGradient>
        <linearGradient id="violetBand" x1="0" y1="1" x2="1" y2="0">
          <stop offset="0" stop-color="#5e1f78"/>
          <stop offset=".5" stop-color="#8a3aa6"/>
          <stop offset="1" stop-color="#6b2586"/>
        </linearGradient>
      </defs>
      <rect class="back-art__field" width="720" height="440" fill="url(#greyField)"/>
      <circle class="back-art__dash" cx="542" cy="376" r="336" fill="none" stroke="#ffffff" stroke-width="2" stroke-dasharray="7 6"/>
      <circle class="back-art__band" cx="542" cy="376" r="310" fill="none" stroke="url(#violetBand)" stroke-width="22"/>
      <circle class="back-art__panel" cx="542" cy="376" r="299" fill="#ffffff"/>
    </svg>

    <div class="watermark">
      <span class="watermark__name">RM Tomás Ledesma</span>
      <span class="watermark__rule"></span>
      <span class="watermark__tagline">Laboratorio de Procesamiento Histológico</span>
    </div>

    <div class="details">
      <p class="details__name">Tomás Ledesma Urquiza M.P 48213</p>
      <p class="details__role">Técnico en Anatomía Patológica</p>
      <p class="details__email">ledesma.tomas@correoviva.com.ar</p>
      <p class="details__address">Av. Duarte Quirós 817 - 2do piso<br>Instituto Brandsen. Córdoba, Argentina</p>
      <p class="details__phone">(0351) 158246093</p>
    </div>
  </section>

</main>
</body>
</html>
```